Business Card Design Project

Looking to update our business cards. We have a logo with our slogan. We are an IT firm so we wouldlike a modern look.

Industry/Entity Type

Business

```html
<!DOCTYPE html>
<html lang="en">
<head>
<meta charset="utf-8">
<title>Corelane — Business Cards</title>
<link rel="stylesheet" href="https://fonts.googleapis.com/css2?family=Jost:wght@400;500&display=swap">
<style>
  :root {
    --brand-green: #6b7f3e;
    --brand-green-soft: rgba(255,255,255,0.22);
    --paper: #ffffff;
    --ink: #2a2a2a;
    --backdrop: #ecebe7;
  }
  * { box-sizing: border-box; margin: 0; padding: 0; }
  html, body { width: 1200px; height: 699px; overflow: hidden; }
  body {
    background: var(--backdrop);
    font-family: "Jost", "Futura", sans-serif;
    display: flex;
    align-items: center;
    justify-content: center;
    gap: 60px;
  }
  .card {
    position: relative;
    width: 525px;
    height: 300px;
    overflow: hidden;
    box-shadow: 0 6px 18px rgba(0,0,0,0.18);
  }

  /* Front */
  .card--front { background: var(--paper); }
  .front__brand {
    position: absolute;
    top: 62px; left: 0; right: 0;
    text-align: center;
  }
  .wordmark {
    display: inline-flex;
    align-items: center;
    gap: 12px;
    font-weight: 500;
    color: var(--brand-green);
  }
  .wordmark__name { font-size: 52px; letter-spacing: 8px; line-height: 1; }
  .wordmark__dot {
    width: 26px; height: 26px; border-radius: 50%;
    background: var(--brand-green);
  }
  .slogan {
    margin-top: 10px;
    font-size: 15px;
    letter-spacing: 4px;
    font-weight: 500;
    color: var(--ink);
    text-transform: uppercase;
  }
  .front__address {
    position: absolute;
    top: 166px; left: 0; right: 0;
    text-align: center;
    font-size: 15px;
    letter-spacing: 0.5px;
    color: var(--ink);
  }
  .front__band {
    position: absolute;
    left: 0; right: 0; bottom: 0;
    height: 104px;
    background: var(--brand-green);
    color: var(--paper);
    padding: 9px 28px;
  }
  .front__band .accent-circle {
    position: absolute;
    right: 70px; top: -42px;
    width: 92px; height: 92px; border-radius: 50%;
    background: var(--brand-green-soft);
  }
  .person { font-size: 18px; font-weight: 500; line-height: 1.3; }
  .person__title { font-weight: 400; font-size: 15px; }
  .contact { list-style: none; margin-top: 3px; font-size: 13px; line-height: 1.45; }
  .contact li { display: flex; align-items: center; gap: 7px; }
  .contact svg { width: 11px; height: 11px; fill: var(--paper); }

  /* Back */
  .card--back {
    background: var(--brand-green);
    color: var(--paper);
  }
  .back__brand {
    position: absolute;
    top: 88px; left: 0; right: 0;
    text-align: center;
  }
  .card--back .wordmark { color: var(--paper); }
  .card--back .wordmark__dot { background: var(--paper); }
  .card--back .slogan { color: var(--paper); }
  .back__web {
    position: absolute;
    bottom: 36px; left: 0; right: 0;
    text-align: center;
    font-size: 22px;
    letter-spacing: 4px;
  }
</style>
</head>
<body>

  <section class="card card--front" aria-label="Business card front">
    <div class="front__brand">
      <div class="wordmark">
        <span class="wordmark__name">CORELANE</span>
        <span class="wordmark__dot"></span>
      </div>
      <p class="slogan">Making Technology Clear</p>
    </div>
    <p class="front__address">00, Complex name, City, State 0042</p>

    <div class="front__band">
      <span class="accent-circle"></span>
      <p class="person">Your Name, <span class="person__title">Title</span></p>
      <ul class="contact">
        <li>
          <svg viewBox="0 0 24 24" aria-hidden="true"><path d="M6.6 10.8a15 15 0 0 0 6.6 6.6l2.2-2.2a1 1 0 0 1 1-.25 11.4 11.4 0 0 0 3.6.57 1 1 0 0 1 1 1V20a1 1 0 0 1-1 1A17 17 0 0 1 3 4a1 1 0 0 1 1-1h3.5a1 1 0 0 1 1 1c0 1.25.2 2.45.57 3.6a1 1 0 0 1-.25 1z"/></svg>
          0987 654321
        </li>
        <li>
          <svg viewBox="0 0 24 24" aria-hidden="true"><path d="M7 1h10a2 2 0 0 1 2 2v18a2 2 0 0 1-2 2H7a2 2 0 0 1-2-2V3a2 2 0 0 1 2-2zm0 3v14h10V4zm5 15.5a1.2 1.2 0 1 0 0 2.4 1.2 1.2 0 0 0 0-2.4z"/></svg>
          0987 654321
        </li>
        <li>
          <svg viewBox="0 0 24 24" aria-hidden="true"><path d="M2 5h20v14H2zm2 2v.4l8 5 8-5V7zm0 2.8V17h16V9.8l-8 5z"/></svg>
          info@corelane.com
        </li>
      </ul>
    </div>
  </section>

  <section class="card card--back" aria-label="Business card back">
    <div class="back__brand">
      <div class="wordmark">
        <span class="wordmark__name">CORELANE</span>
        <span class="wordmark__dot"></span>
      </div>
      <p class="slogan">Making Technology Clear</p>
    </div>
    <p class="back__web">www.corelane.com</p>
  </section>

</body>
</html>
```